Business Card For Halvenmoor Financial Consulting

Hi, I would like a business card designed. Bold, modern.
Please use the same design as the logo. I have also attached the website design to see the overall theme.
Wordmark Font
Color: Hex: #01AEF7

```html
<!DOCTYPE html>
<html lang="en">
<head>
<meta charset="utf-8">
<title>Halvenmoor Financial Consulting – Business Card</title>
<link href="https://fonts.googleapis.com/css2?family=Open+Sans:wght@400;700&display=swap" rel="stylesheet">
<style>
  :root{
    --backdrop:#232323;
    --paper:#ffffff;
    --navy:#0b4470;
    --navy-deep:#0a3f66;
    --sky:#2b9fe0;
    --mist:#dce9f8;
    --ink:#1a1a1a;
  }
  *{box-sizing:border-box;margin:0;padding:0}
  html,body{width:1200px;height:780px;overflow:hidden;background:var(--backdrop)}
  body{font-family:"Open Sans",Arial,sans-serif;position:relative}
  .card{position:absolute;top:235px;width:540px;height:310px;box-shadow:0 14px 30px rgba(0,0,0,.45);overflow:hidden}
  .card--front{left:40px;background:var(--paper)}
  .card--back{left:620px;background:var(--navy-deep)}

  .front__mark{position:absolute;left:30px;top:28px;width:150px;height:150px;border:16px solid var(--mist)}
  .front__person{position:absolute;left:44px;top:52px}
  .person__name{font-size:27px;font-weight:700;color:var(--navy);line-height:1.1}
  .person__role{font-size:13px;color:var(--ink);margin-top:2px}

  .wordmark{position:absolute;right:34px;top:62px;text-align:right;color:var(--navy);font-weight:700;line-height:1.05}
  .wordmark__line{display:block;font-size:30px;letter-spacing:1px;text-transform:uppercase}
  .wordmark__sub{display:block;font-size:13px;letter-spacing:5px;text-transform:uppercase}

  .address{position:absolute;right:34px;top:160px;text-align:right;font-size:14px;color:var(--ink);line-height:1.4}
  .contacts{position:absolute;right:34px;bottom:22px;list-style:none;font-size:14px;color:var(--ink)}
  .contacts li{display:flex;justify-content:flex-end;align-items:center;gap:8px;line-height:1.55}
  .contacts svg{width:14px;height:14px;flex:none}

  .back__wordmark{position:absolute;right:36px;bottom:44px;text-align:right;color:var(--paper);font-weight:700;line-height:1.05}
  .back__wordmark .wordmark__line{font-size:32px}
</style>
</head>
<body>
  <section class="card card--front" aria-label="Card front">
    <div class="front__mark" aria-hidden="true"></div>
    <div class="front__person">
      <p class="person__name">Mirela Vostrand</p>
      <p class="person__role">Managing Director</p>
    </div>
    <p class="wordmark">
      <span class="wordmark__line">Halvenmoor</span>
      <span class="wordmark__sub">Financial Consulting</span>
    </p>
    <p class="address">418 Larchmont Ave. Suite 310<br>Ashbury, TX 75520</p>
    <ul class="contacts">
      <li>(555) 214-6630
        <svg viewBox="0 0 16 16" aria-hidden="true"><path fill="#2b9fe0" d="M4 1.5l2.2 2.6-1.3 1.6a8 8 0 0 0 5.4 5.4l1.6-1.3 2.6 2.2-1.4 2A3 3 0 0 1 10 15 10 10 0 0 1 1 6a3 3 0 0 1 1-2.1z"/></svg>
      </li>
      <li>hello@halvenmoor.com
        <svg viewBox="0 0 16 16" aria-hidden="true"><rect x="1" y="3" width="14" height="10" rx="1.5" fill="#2b9fe0"/><path d="M1.5 4l6.5 5 6.5-5" fill="none" stroke="#fff" stroke-width="1.3"/></svg>
      </li>
      <li>www.halvenmoor.com
        <svg viewBox="0 0 16 16" aria-hidden="true"><circle cx="8" cy="8" r="7" fill="#2b9fe0"/><path d="M1 8h14M8 1c-3 3.5-3 10.5 0 14M8 1c3 3.5 3 10.5 0 14" fill="none" stroke="#fff" stroke-width="1"/></svg>
      </li>
    </ul>
  </section>

  <section class="card card--back" aria-label="Card back">
    <p class="back__wordmark">
      <span class="wordmark__line">Halvenmoor</span>
      <span class="wordmark__sub">Financial Consulting</span>
    </p>
  </section>
</body>
</html>
```